New Business Card Design

We need a business card design for a new company based in Sydney called "Haven and Hue". This is an online buisness which will have an online store providing imported homewares.
We are looking for something that is different, perhaps even in shape and using the logo that was designed by Pixel Harbor.

Attached document is a basic example I want to see more creative versions.

Target Market(s)

Homewares, Interior Design

Industry/Entity Type

Business

Contact Information for Business Card

Company Logo
Company Name
Industry area
Name
Position
Phone
Email
Website
Motto

Requirements
Must have
• Logo
Nice to have
• Social website logos - Chatterloop, Glimmoraly, Quibbly, Boardlyne, Veltrix+

```html
<!DOCTYPE html>
<html lang="en">
<head>
<meta charset="utf-8">
<title>Haven and Hue – Business Card</title>
<link href="https://fonts.googleapis.com/css2?family=Lato:wght@400;700&display=swap" rel="stylesheet">
<style>
  :root {
    --backdrop: #d3d3d1;
    --ink: #0b0b0b;
    --paper: #ffffff;
    --gold: #c08a3e;
    --gold-light: #e6c27a;
    --gold-deep: #8e5f22;
    --badge: #262626;
    --text-light: #f2f2f2;
  }
  * { margin: 0; padding: 0; box-sizing: border-box; }
  html, body { width: 1200px; height: 1000px; overflow: hidden; }
  body {
    background: var(--backdrop);
    font-family: "Lato", sans-serif;
    position: relative;
  }
  .card {
    position: absolute;
    width: 600px;
    height: 350px;
    border-radius: 18px;
    overflow: hidden;
    box-shadow: 0 6px 18px rgba(0,0,0,0.18);
  }
  .card svg.card-art { position: absolute; inset: 0; }

  /* Back of card */
  .card-back { left: 80px; top: 80px; background: var(--ink); }
  .back-badge {
    position: absolute; left: 190px; top: 65px;
    width: 220px; height: 220px; border-radius: 50%;
    background: var(--badge);
    display: flex; align-items: center; justify-content: center; text-align: center;
  }
  .brand-name {
    font-family: "Lato", sans-serif;
    font-weight: 400;
    color: var(--text-light);
    line-height: 1.15;
  }
  .back-badge .brand-name { font-size: 32px; }

  /* Front of card */
  .card-front { left: 520px; top: 570px; background: var(--paper); }
  .front-badge {
    position: absolute; left: 82px; top: 62px;
    width: 176px; height: 176px; border-radius: 50%;
    background: var(--ink);
    display: flex; align-items: center; justify-content: center; text-align: center;
  }
  .front-badge .brand-name { font-size: 26px; }

  .contact-block {
    position: absolute; right: 52px; top: 82px;
    text-align: right; color: var(--text-light);
  }
  .contact-name { font-weight: 700; font-size: 22px; color: var(--gold); }
  .contact-role { font-size: 16px; margin-bottom: 22px; }
  .contact-line { font-size: 13.5px; line-height: 1.45; letter-spacing: 0.2px; }
  .contact-phone { letter-spacing: 3px; }

  .social-row {
    position: absolute; left: 22px; bottom: 14px;
    display: flex; gap: 10px; align-items: center;
  }
  .social-item {
    display: flex; align-items: center; gap: 4px;
    font-size: 9.5px; color: var(--gold);
  }
  .social-dot { width: 10px; height: 10px; border-radius: 50%; background: var(--gold); }
</style>
</head>
<body>

  <section class="card card-back" aria-label="Card back">
    <div class="back-badge">
      <span class="brand-name">Haven<br>and Hue</span>
    </div>
  </section>

  <section class="card card-front" aria-label="Card front">
    <svg class="card-art" viewBox="0 0 600 350" width="600" height="350" aria-hidden="false">
      <defs>
        <linearGradient id="goldSweep" x1="0" y1="1" x2="1" y2="0">
          <stop offset="0" stop-color="var(--gold-deep)"/>
          <stop offset="0.4" stop-color="var(--gold-light)"/>
          <stop offset="0.75" stop-color="var(--gold)"/>
          <stop offset="1" stop-color="var(--gold-light)"/>
        </linearGradient>
      </defs>
      <path class="dark-field" fill="var(--ink)"
            d="M0,292 C200,302 300,262 362,150 C402,62 422,22 452,0 L565,0 L565,350 L0,350 Z"/>
      <rect class="dark-corner" x="565" y="262" width="35" height="88" fill="var(--ink)"/>
      <rect class="dark-top" x="452" y="0" width="148" height="40" fill="var(--paper)"/>
      <path class="dark-top-edge" fill="var(--ink)" d="M440,40 L565,40 L565,0 L452,0 Z"/>
      <path class="gold-swoosh" fill="url(#goldSweep)"
            d="M0,266 C200,282 298,244 352,146 C392,56 412,20 444,0 L452,0 C422,22 402,62 362,150 C300,262 200,302 0,292 Z"/>
      <ellipse role="img" aria-label="Small gold leaf sprig ornament" cx="462" cy="16" rx="9" ry="14" fill="var(--gold)"/>

      <g class="contact-icons" fill="var(--gold)">
        <!-- phone -->
        <path d="M576,184 q0,-5 5,-5 h8 q5,0 5,5 v2 h-4 v-2 h-10 v2 h-4 Z M577,188 h16 l2,9 h-20 Z"/>
        <!-- mail -->
        <rect x="575" y="207" width="20" height="14" rx="1.5"/>
        <path d="M576,208 L585,215 L594,208" fill="none" stroke="var(--paper)" stroke-width="1.6"/>
        <!-- globe -->
        <circle cx="585" cy="241" r="10"/>
        <g fill="none" stroke="var(--paper)" stroke-width="1.2">
          <ellipse cx="585" cy="241" rx="4.5" ry="10"/>
          <line x1="575" y1="241" x2="595" y2="241"/>
          <line x1="577" y1="236" x2="593" y2="236"/>
          <line x1="577" y1="246" x2="593" y2="246"/>
        </g>
      </g>
    </svg>

    <div class="front-badge">
      <span class="brand-name">Haven<br>and Hue</span>
    </div>

    <div class="contact-block">
      <p class="contact-name">Mara Ellison</p>
      <p class="contact-role">Director</p>
      <p class="contact-line">Unit 0, Harbour Lane</p>
      <p class="contact-line">Lowmere 1234 Queensland AU</p>
      <p class="contact-line contact-phone">07 9876 5432</p>
      <p class="contact-line">me@havenandhue.com.au</p>
      <p class="contact-line">www.havenandhue.com.au</p>
    </div>

    <ul class="social-row">
      <li class="social-item"><span class="social-dot"></span>Chatterloop</li>
      <li class="social-item"><span class="social-dot"></span>Quibbly</li>
      <li class="social-item"><span class="social-dot"></span>Glimmoraly</li>
      <li class="social-item"><span class="social-dot"></span>Boardlyne</li>
      <li class="social-item"><span class="social-dot"></span>Veltrix+</li>
    </ul>
  </section>

</body>
</html>
```